BrivoTerna. Lantern of the Steady Harvest. Business card

Professional business card for BrivoTerna (Lantern of the Steady Harvest)
My rationale: Strategy-> Execution-> Results-> Value that lead to the BrivoTerna name: We put the Lantern of the Steady Harvest.
We deliver value to our customers helping them at defining a good strategy (cyan arrow). 90% of well formulated strategies fail due to poor execution so we also consider strategical execution very important (green arrow). Due to the execution we obtain the results (blue arrow). Finally, the results provide feedback to redefine strategy, and the new strategy has to be executed and new results obtained providing new feedback and on and on. It's like a wheel that finally, must create corporate value: value for shareholders, staholders, employees, providers...-

Target Market(s)

CEOs and steering comitees , invewrnent funds

Industry/Entity Type

Business Consultant

Contact Information for Business Card

Teodoro Vinsquel
CEO & Founder
teodoro.vinsquel@brivoterna-example.com
Mobile: +34 655.803.912
www.brivoterna-example.com

Colors

Designer to choose colors to be used in the design.

Requirements
Nice to have
• Nice to hace the words: Strategy, execution, results
• Nice to vave the claim: Lantern of the Steady Harvest
• The three colors should be shown:
• cyan for STRATEGY
• green for EXECUTION
• blue for RESULTS
Should not have
• Complete black background

```html
<!DOCTYPE html>
<html lang="en">
<head>
<meta charset="utf-8">
<title>BrivoTerna – Business Card</title>
<link rel="stylesheet" href="https://fonts.googleapis.com/css2?family=Open+Sans:wght@400;700&display=swap">
<style>
  :root {
    --backdrop: #dcdcdc;
    --navy: #234091;
    --cyan: #25ace3;
    --green: #9aca3c;
    --white: #ffffff;
  }
  html, body {
    margin: 0;
    padding: 0;
    width: 1200px;
    height: 1200px;
    overflow: hidden;
    background: var(--backdrop);
  }
  .sheet {
    display: block;
    width: 1200px;
    height: 1200px;
  }
  .sheet text { font-family: "Open Sans", Arial, sans-serif; }
  .card-base { fill: var(--navy); }
  .band-green { fill: var(--green); }
  .band-cyan { fill: var(--cyan); }
  .panel-white { fill: var(--white); }
  .holder-name { fill: var(--white); font-weight: 700; font-size: 44px; }
  .holder-role { fill: var(--cyan); font-weight: 400; font-size: 36px; }
  .role-rule { fill: var(--green); }
  .contact-line { fill: var(--white); font-weight: 400; font-size: 30px; }
  .contact-line--email { font-size: 29px; }
  .icon-disc { fill: var(--white); }
  .icon-glyph { fill: var(--navy); }
  .icon-stroke { fill: none; stroke: var(--navy); stroke-width: 3; }
  .brand-name { font-weight: 700; font-size: 72px; letter-spacing: -1px; }
  .brand-name--front { fill: var(--navy); }
  .brand-name--back { fill: var(--white); font-size: 82px; }
  .back-web { fill: var(--white); font-weight: 400; font-size: 30px; }
</style>
</head>
<body>
<svg class="sheet" viewBox="0 0 1932 1932" xmlns="http://www.w3.org/2000/svg" role="img" aria-label="BrivoTerna business card, front and back">
  <defs>
    <clipPath id="front-clip">
      <rect x="0" y="0" width="1170" height="668" rx="30"/>
    </clipPath>
  </defs>

  <!-- Front of card -->
  <g class="card-front" transform="translate(378 190)">
    <g clip-path="url(#front-clip)">
      <rect class="card-base" x="0" y="0" width="1170" height="668"/>
      <path class="band-green" d="M0 0 L777 0 C680 60 600 220 482 475 C430 580 380 625 324 668 L0 668 Z"/>
      <path class="band-cyan" d="M0 0 L484 0 C560 170 560 340 482 475 C430 580 380 625 324 668 L0 668 Z"/>
      <path class="panel-white" d="M0 0 L290 0 C420 90 500 220 497 355 C494 470 430 580 324 668 L0 668 Z"/>
    </g>

    <text class="brand-name brand-name--front" x="234" y="430" text-anchor="middle">BrivoTerna</text>

    <text class="holder-name" x="1129" y="170" text-anchor="end">Teodoro Vinsquel</text>
    <text class="holder-role" x="1129" y="217" text-anchor="end">CEO &amp; Founder</text>
    <rect class="role-rule" x="1028" y="243" width="102" height="4"/>

    <g class="contact-row">
      <text class="contact-line" x="1052" y="383" text-anchor="end">+34 655.803.912</text>
      <circle class="icon-disc" cx="1102" cy="373" r="28"/>
      <rect class="icon-stroke" x="1093" y="359" width="18" height="28" rx="3"/>
      <circle class="icon-glyph" cx="1102" cy="381" r="2.5"/>
    </g>
    <g class="contact-row">
      <text class="contact-line" x="1052" y="460" text-anchor="end">www.brivoterna-example.com</text>
      <circle class="icon-disc" cx="1102" cy="450" r="28"/>
      <circle class="icon-glyph" cx="1102" cy="450" r="13"/>
      <path d="M1089 450 H1115 M1102 437 V463" stroke="var(--white)" stroke-width="1.5"/>
    </g>
    <g class="contact-row">
      <text class="contact-line contact-line--email" x="1052" y="538" text-anchor="end">teodoro.vinsquel@brivoterna-example.com</text>
      <circle class="icon-disc" cx="1102" cy="528" r="28"/>
      <path class="icon-glyph" d="M1115 516 L1087 528 L1098 532 L1102 542 Z"/>
    </g>
  </g>

  <!-- Back of card -->
  <g class="card-back" transform="translate(378 1067)">
    <rect class="card-base" x="0" y="0" width="1170" height="668" rx="30"/>
    <text class="brand-name brand-name--back" x="585" y="441" text-anchor="middle">BrivoTerna</text>
    <text class="back-web" x="1114" y="618" text-anchor="end">www.brivoterna-example.com</text>
  </g>
</svg>
</body>
</html>
```